Business Card: RW Office Partners - Your organised problem solver

Business Name: RW Office Partners
Website: www.rwofficepartners.com.au
Email: marisol@rwofficepartners.com.au
Mobile: 61 482 907 236
Facebook: @rwofficepartners
Instrgram: @rwofficepartners

Brading Colours:
HEX
#986474
#ddccd3
#7a8498
#c9d8e4
#000000
#ffffff

Tag Line: Your organised problem solver

Link to DRAFT website:
https://deskhelpcollective.wixsite.com/rw-office-partners

About Page from the website:
My name is Marisol Wrenfield, and I would love to assist you to become more productive in your day to day and achieve your business and personal goals.
My mission is to give you time, time to work on the important tasks of your business or to be able to spend more time with your family. I will take on the tasks you don’t have time for, don’t know well or simply don’t like to do.
I have an extensive background in Administration, Tender Coordination, Document Control, WHS and Quality Management working primarily in the Construction, Mining and Corporate World.
I am passionate about being organised, having order and making things in your life (and mine) easier! I love to watch something unfold and grow into something amazing! I am known for being the go-to problem solver, the organiser of all things, producing high standards of work even under pressure. I’m also a confident communicator, and I understand that you’re busy running your business.

Target Market(s)

Small to Medium Business who require assistance in their business by a virtual assistant.

Industry/Entity Type

Virtual Assistant

Contact Information for Business Card

Mobile: 61 482 907 236

Font styles to use
Sans Serif

Colors
ffffff

Requirements
Must have
• Branding Colours as outlined.
Contact Details as outlined.
Logo as provided.
Proper contact details - mobile, facebook, instragm, website.
Simple, Elegant, very clean looking.
Should not have
• Note cute with pictures.
Not too girly as still want to market to construction companies.

```html
<!DOCTYPE html>
<html lang="en">
<head>
<meta charset="utf-8">
<title>RW Office Partners – Business Card</title>
<link href="https://fonts.googleapis.com/css2?family=Nunito:wght@400;600;700&family=Roboto:wght@400&display=swap" rel="stylesheet">
<style>
  :root {
    --brand-plum: #986474;
    --card-plum: #8a5d6c;
    --brand-slate: #7a8498;
    --ink: #222222;
    --paper: #ffffff;
    --backdrop: #6b6768;
  }
  * { margin: 0; padding: 0; box-sizing: border-box; }
  html, body { width: 1200px; height: 1200px; overflow: hidden; }
  body {
    position: relative;
    background: var(--backdrop);
    font-family: "Roboto", Arial, sans-serif;
  }
  .card {
    position: absolute;
    width: 712px;
    height: 418px;
    border-radius: 26px;
    overflow: hidden;
  }
  .card--front { left: 244px; top: 118px; background: var(--card-plum); }
  .card--back  { left: 244px; top: 644px; background: var(--paper); }

  .front-name {
    position: absolute;
    left: 0; right: 0; top: 180px;
    text-align: center;
    font-family: "Nunito", Arial, sans-serif;
    font-weight: 700;
    font-size: 50px;
    letter-spacing: 0.5px;
    color: var(--paper);
  }

  .brand-block { position: absolute; left: 30px; top: 162px; width: 300px; }
  .brand-name {
    font-family: "Nunito", Arial, sans-serif;
    font-weight: 700;
    font-size: 29px;
    color: var(--brand-plum);
    white-space: nowrap;
  }
  .brand-tagline {
    margin-top: 12px;
    font-family: "Nunito", Arial, sans-serif;
    font-weight: 400;
    font-size: 18px;
    color: #333;
    white-space: nowrap;
  }

  .contact-block { position: absolute; left: 337px; top: 102px; }
  .person-name {
    font-family: "Nunito", Arial, sans-serif;
    font-weight: 700;
    font-size: 25px;
    color: var(--brand-plum);
  }
  .person-role { margin-top: 2px; font-size: 17px; color: #333; }
  .contact-list { list-style: none; margin-top: 26px; }
  .contact-list li {
    display: flex; align-items: center;
    height: 26px;
    font-size: 18px;
    color: var(--ink);
  }
  .contact-icon { width: 16px; height: 16px; margin: 0 14px 0 2px; flex: none; }
</style>
</head>
<body>

  <section class="card card--front">
    <div class="front-name">RW Office Partners</div>
  </section>

  <section class="card card--back">
    <div class="brand-block">
      <div class="brand-name">RW Office Partners</div>
      <div class="brand-tagline">Your organised problem solver</div>
    </div>

    <div class="contact-block">
      <div class="person-name">Marisol Wrenfield</div>
      <div class="person-role">Virtual Assistant</div>
      <ul class="contact-list">
        <li>
          <svg class="contact-icon" viewBox="0 0 16 16" aria-hidden="true">
            <path d="M1 6c0-2 3-3 7-3s7 1 7 3v1h-3V5.5H4V7H1z M3.5 8h9l1.5 5H2z" fill="var(--brand-plum)"/>
            <circle cx="8" cy="10.5" r="1.4" fill="#fff"/>
          </svg>
          61 482 907 236
        </li>
        <li>
          <svg class="contact-icon" viewBox="0 0 16 16" aria-hidden="true">
            <rect x="1" y="3" width="14" height="10" fill="var(--brand-plum)"/>
            <path d="M1 3l7 6 7-6" fill="none" stroke="#fff" stroke-width="1.3"/>
          </svg>
          marisol@rwofficepartners.com.au
        </li>
        <li>
          <svg class="contact-icon" viewBox="0 0 16 16" aria-hidden="true">
            <g fill="none" stroke="var(--brand-plum)" stroke-width="1.3">
              <circle cx="8" cy="8" r="6.5"/>
              <ellipse cx="8" cy="8" rx="3" ry="6.5"/>
              <path d="M1.5 8h13M2.5 4.8h11M2.5 11.2h11"/>
            </g>
          </svg>
          www.rwofficepartners.com.au
        </li>
        <li>
          <svg class="contact-icon" viewBox="0 0 16 16" aria-hidden="true">
            <rect x="1" y="1" width="14" height="14" rx="2" fill="var(--brand-plum)"/>
          </svg>
          @rwofficepartners
        </li>
        <li>
          <svg class="contact-icon" viewBox="0 0 16 16" aria-hidden="true">
            <circle cx="8" cy="8" r="7" fill="var(--brand-plum)"/>
          </svg>
          @rwofficepartners
        </li>
      </ul>
    </div>
  </section>

</body>
</html>
```